Children's Autism Center Seeking New Advertising Document

Maplebrook Autism Center, a children's autism therapy center in Indiana is seeking to revamp our advertising efforts. We want to combined all of the various advertising documents we use now into one, new, eye catching document that we can handout to parents during tours, or prospective clients at our various events. The final design should be unique, eye catching, non-clinical and convey a feeling of hope for families.

I have provided a microsoft publisher document with a basic idea of what we would like. Please use the text from the document but feel free to make any additional artistic changes. The back of the document has an image of a puzzle. We would like each point listed around those puzzle pieces to be inside a piece of a puzzle (feel free to select or design your own puzzle piece image).

The front of the document needs some work. Please create a new design for the front of the document. Make sure to include the photo, the Maplebrook Autism Center logo, and the catchphrase.

Industry/Entity Type

Healthcare

Font styles to use
Other font styles liked:
• Calibri

Colors
33a6d7
0592cd
acd036
fbee3d

Requirements
Must have
• The design is a 3 panel gate fold and it is an 11 in x 17 in document. Please see the attached publisher and pdf file for an idea of what we want and how to use the information provided.

```html
<!DOCTYPE html>
<html lang="en">
<head>
<meta charset="utf-8">
<title>Maplebrook Autism Center – Gate Fold Brochure</title>
<link rel="stylesheet" href="https://fonts.googleapis.com/css2?family=Lato:wght@400;700;900&family=Roboto+Slab:wght@700;800&display=swap">
<style>
  :root {
    --blue: #0592cd;
    --blue-light: #33a6d7;
    --blue-deep: #1b6fb3;
    --green: #acd036;
    --yellow: #fbee3d;
    --grey: #6d6e71;
    --grey-dark: #4d4e50;
    --ink: #2b2b2b;
    --body: #3c3c3c;
    --paper: #ffffff;
    --backdrop: #ece8e2;
    --photo-room: linear-gradient(180deg, #d3ce98 0%, #b9ad8c 55%, #8f8373 100%);
    --photo-portrait: linear-gradient(180deg, #e6d8c8 0%, #c9b49d 100%);
    --photo-group: linear-gradient(180deg, #eeebe6 0%, #cfc3b4 100%);
  }
  * { box-sizing: border-box; margin: 0; padding: 0; }
  html, body { width: 1200px; height: 907px; overflow: hidden; }
  body { background: var(--backdrop); font-family: "Lato", sans-serif; color: var(--body); position: relative; }

  .spread { position: absolute; top: 246px; width: 580px; height: 414px; background: var(--paper); overflow: hidden; }
  .spread--outside { left: 12px; }
  .spread--inside { left: 608px; }
  .spread > * { position: absolute; }
  .shapes { left: 0; top: 0; width: 580px; height: 414px; }

  .photo { background: var(--photo-room); }
  .photo--round { border-radius: 50%; border: 4px solid var(--blue); background: var(--photo-portrait); box-shadow: 0 0 0 2px #fff inset; }
  .photo--group { background: var(--photo-group); border-radius: 6px; }

  .lorem { font-size: 6px; line-height: 1.32; text-align: justify; color: var(--body); }

  /* outside spread */
  .cover-title { left: 8px; top: 318px; width: 142px; font-family: "Roboto Slab", serif; font-weight: 800; color: var(--blue-deep); font-size: 15.5px; line-height: 1.05; letter-spacing: .2px; }
  .cover-tagline { left: 8px; top: 355px; width: 142px; font-size: 8.6px; color: var(--grey-dark); }
  .cover-web { left: 12px; top: 394px; font-size: 7.4px; font-weight: 700; color: #fff; letter-spacing: .9px; }
  .headline { left: 150px; top: 9px; width: 282px; text-align: center; }
  .headline__kicker { font-family: "Roboto Slab", serif; font-weight: 800; color: var(--yellow); font-size: 14px; letter-spacing: .4px; }
  .headline__main { font-size: 19.5px; color: #fff; letter-spacing: .3px; margin-top: 1px; }
  .col { top: 122px; width: 128px; }
  .col--a { left: 160px; }
  .col--b { left: 298px; }
  .brand { font-family: "Lato", sans-serif; font-weight: 900; font-size: 11px; line-height: 1.05; display: flex; align-items: center; gap: 5px; }
  .brand__dot { width: 12px; height: 12px; border-radius: 50%; background: currentColor; flex: none; }
  .brand--band { left: 162px; top: 368px; color: #fff; }
  .brand--panel { left: 446px; top: 362px; color: var(--blue); }
  .band-web { left: 306px; top: 380px; font-size: 7px; font-weight: 700; color: #fff; letter-spacing: 1px; }

  /* inside spread */
  .panel-title { font-size: 9.6px; font-weight: 900; color: var(--ink); line-height: 1.2; }
  .panel-title--parents { left: 8px; top: 6px; width: 140px; }
  .panel-title--approach { left: 434px; top: 12px; width: 142px; }
  .parents-body { left: 8px; top: 133px; width: 138px; }
  .stories-title { left: 152px; top: 9px; width: 276px; text-align: center; font-size: 11.5px; font-weight: 700; color: #fff; }
  .stories-sub { left: 152px; top: 38px; width: 276px; text-align: center; font-size: 9.6px; font-weight: 700; color: var(--ink); }
  .story-photo { width: 48px; height: 48px; border-width: 3px; }
  .story { width: 84px; font-size: 5.8px; line-height: 1.3; text-align: center; color: var(--body); }
  .perspective-title { left: 152px; top: 353px; width: 276px; text-align: center; font-size: 9.6px; font-weight: 700; color: #fff; }
  .perspective-body { left: 164px; top: 368px; width: 254px; font-size: 5.8px; line-height: 1.3; text-align: center; color: #f1f1f1; }
  .approach-lead { left: 434px; top: 78px; width: 142px; font-size: 8.8px; font-weight: 900; color: var(--ink); line-height: 1.25; }
  .approach-list { left: 434px; top: 160px; width: 142px; list-style: none; }
  .approach-list li { font-size: 5.8px; line-height: 1.3; padding-left: 7px; margin-bottom: 5px; position: relative; }
  .approach-list li::before { content: ""; position: absolute; left: 0; top: 1.5px; width: 4px; height: 4px; border-radius: 50%; background: var(--green); }
</style>
</head>
<body>

<!-- Outside of the gate fold: left flap, back panel, cover -->
<section class="spread spread--outside" aria-label="Brochure outside">
  <div class="photo" style="left:0;top:0;width:150px;height:310px" role="img" aria-label="Photo of children and therapists playing together in a classroom"></div>
  <div class="photo" style="left:432px;top:0;width:148px;height:310px" role="img" aria-label="Photo of children and therapists playing together in a classroom"></div>

  <svg class="shapes" viewBox="0 0 580 414" aria-hidden="true">
    <defs>
      <linearGradient id="sun" x1="0" y1="0" x2="1" y2="0"><stop offset="0" stop-color="#fbee3d"/><stop offset="1" stop-color="#acd036"/></linearGradient>
      <linearGradient id="sky" x1="0" y1="0" x2="0" y2="1"><stop offset="0" stop-color="#0592cd"/><stop offset="1" stop-color="#33a6d7"/></linearGradient>
      <linearGradient id="slate" x1="0" y1="0" x2="0" y2="1"><stop offset="0" stop-color="#8a8b8e"/><stop offset="1" stop-color="#58595b"/></linearGradient>
    </defs>
    <!-- left flap -->
    <path d="M0,0 H150 V18 Q80,14 0,72 Z" fill="url(#sun)"/>
    <path d="M0,80 Q70,22 150,24" fill="none" stroke="#0592cd" stroke-width="5"/>
    <path d="M0,292 Q70,258 150,268 V290 Q70,282 0,316 Z" fill="url(#sun)"/>
    <path d="M0,318 Q70,284 150,292 V414 H0 Z" fill="#f4f4f4"/>
    <path d="M0,318 Q70,284 150,292" fill="none" stroke="#0592cd" stroke-width="4"/>
    <rect x="0" y="391" width="150" height="16" fill="url(#slate)"/>
    <!-- back panel -->
    <rect x="150" y="0" width="282" height="414" fill="#fff"/>
    <path d="M150,0 H432 V90 Q300,78 150,110 Z" fill="url(#sky)"/>
    <path d="M150,116 Q300,84 432,97" fill="none" stroke="#acd036" stroke-width="4"/>
    <path d="M150,310 Q290,292 432,304" fill="none" stroke="#fbee3d" stroke-width="5"/>
    <path d="M150,322 Q290,300 432,314" fill="none" stroke="#0592cd" stroke-width="6"/>
    <path d="M150,333 Q290,312 432,324" fill="none" stroke="#acd036" stroke-width="4"/>
    <path d="M150,342 Q290,320 432,332 V414 H150 Z" fill="url(#slate)"/>
    <!-- cover -->
    <path d="M432,0 H580 V22 Q500,12 432,30 Z" fill="url(#sun)"/>
    <path d="M432,290 Q510,262 580,270 V292 Q510,284 432,314 Z" fill="url(#sun)"/>
    <path d="M432,316 Q510,286 580,294 V414 H432 Z" fill="#f4f4f4"/>
    <path d="M432,316 Q510,286 580,294" fill="none" stroke="#0592cd" stroke-width="4"/>
  </svg>

  <div class="photo photo--round" style="left:-6px;top:30px;width:72px;height:72px" role="img" aria-label="Portrait photo of a smiling toddler"></div>
  <div class="photo photo--round" style="left:444px;top:8px;width:90px;height:90px" role="img" aria-label="Photo of a therapist working with a young boy at a table"></div>
  <div class="photo photo--round" style="left:548px;top:10px;width:70px;height:70px" role="img" aria-label="Portrait photo of a smiling toddler"></div>

  <h1 class="cover-title">MAPLEBROOK<br>AUTISM CENTER</h1>
  <p class="cover-tagline">Hope for every Child,every famly</p>
  <p class="cover-web">www.company website.com</p>

  <div class="headline">
    <p class="headline__kicker">SOLVING THE AUISMPUZZLE</p>
    <p class="headline__main">THE MAPLEBROOK WAY!</p>
  </div>

  <div class="col col--a lorem">
    <p>Lorem ipsum dolor sit amet, modus legere rationibus has an, veritus definiebas eu eum, mea patrioque cotidieque et. Ex inani adipisci conceptam sit, illique aliquid no nec. Verear interpretaris vituperatoribus ea his, mei ad illum suscipiantur. Solum integre sed ex, cu odio alii vocent cum. Per graece maiorum in, ad posse inani iracundia nec, vim an quaeque scaevola appetere. Est ut erat numquam inermis. Paulo possim ne nam.</p>
    <p>Cum an essent omnium, cum ut sale legendos invenire. Has probatus molestiae eu, vis ut aperiri insolens. Et his nemore platonem, ut adhuc suavitate erroribus est, id noster volutpat duo. Tota laudem malorum nec ex, iusto cotidieque per ex. Pri ei prima nullam efficiantur.</p>
    <p>Ea duo duis luptatum singulis. Per diceret elaboraret ea, pri graeci eloquentiam te, commune invidunt ne vel. Possit petentium ne eum. At mel vero lorem aeterno, sed eu dolor oratio eligendi.</p>
  </div>
  <div class="col col--b lorem">
    <p>Lorem ipsum dolor sit amet, modus legere rationibus has an, veritus definiebas eu eum, mea patrioque cotidieque et. Ex inani adipisci conceptam sit, illique aliquid no nec. Verear interpretaris vituperatoribus ea his, mei ad illum suscipiantur. Solum integre sed ex, cu odio alii vocent cum. Per graece maiorum in, ad posse inani iracundia nec, vim an quaeque scaevola appetere. Est ut erat numquam inermis. Paulo possim ne nam.</p>
    <p>Cum an essent omnium, cum ut sale legendos invenire. Has probatus molestiae eu, vis ut aperiri insolens. Et his nemore platonem, ut adhuc suavitate erroribus est, id noster volutpat duo. Tota laudem malorum nec ex, iusto cotidieque per ex. Pri ei prima nullam efficiantur.</p>
    <p>Ea duo duis luptatum singulis. Per diceret elaboraret ea, pri graeci eloquentiam te, commune invidunt ne vel. Possit petentium ne eum. At mel vero lorem aeterno, sed eu dolor oratio eligendi.</p>
  </div>

  <p class="brand brand--band"><span class="brand__dot"></span><span>Maplebrook<br>Autism Center</span></p>
  <p class="band-web">www.company website.com</p>
  <p class="brand brand--panel"><span class="brand__dot"></span><span>Maplebrook<br>Autism Center</span></p>
</section>

<!-- Inside of the gate fold -->
<section class="spread spread--inside" aria-label="Brochure inside">
  <svg class="shapes" viewBox="0 0 580 414" aria-hidden="true">
    <defs>
      <linearGradient id="sun2" x1="0" y1="0" x2="1" y2="0"><stop offset="0" stop-color="#fbee3d"/><stop offset="1" stop-color="#acd036"/></linearGradient>
      <linearGradient id="sky2" x1="0" y1="0" x2="0" y2="1"><stop offset="0" stop-color="#0592cd"/><stop offset="1" stop-color="#33a6d7"/></linearGradient>
      <linearGradient id="slate2" x1="0" y1="0" x2="0" y2="1"><stop offset="0" stop-color="#8a8b8e"/><stop offset="1" stop-color="#58595b"/></linearGradient>
      <linearGradient id="mist" x1="0" y1="0" x2="0" y2="1"><stop offset="0" stop-color="#ffffff"/><stop offset="1" stop-color="#ececec"/></linearGradient>
    </defs>
    <!-- parents panel -->
    <path d="M0,0 H152 V50 Q90,40 0,72 Z" fill="url(#sun2)"/>
    <path d="M0,80 Q90,50 152,58" fill="none" stroke="#0592cd" stroke-width="5"/>
    <path d="M0,86 Q90,58 152,66" fill="none" stroke="#acd036" stroke-width="3"/>
    <path d="M0,370 Q70,330 152,342" fill="none" stroke="#fbee3d" stroke-width="5"/>
    <!-- stories panel -->
    <rect x="152" y="0" width="276" height="414" fill="url(#mist)"/>
    <path d="M152,0 H428 V26 Q290,40 152,32 Z" fill="url(#sky2)"/>
    <path d="M152,60 Q290,50 428,58" fill="none" stroke="#33a6d7" stroke-width="2"/>
    <path d="M152,334 Q290,316 428,330" fill="none" stroke="#acd036" stroke-width="6"/>
    <path d="M152,344 Q290,326 428,338 V414 H152 Z" fill="url(#slate2)"/>
    <!-- approach panel -->
    <path d="M428,0 H580 V22 Q500,34 428,26 Z" fill="url(#sun2)"/>
    <path d="M428,30 Q500,30 580,58 V70 Q500,42 428,38 Z" fill="url(#sky2)"/>
    <path d="M428,44 Q500,48 580,76" fill="none" stroke="#acd036" stroke-width="3"/>
    <line x1="152" y1="0" x2="152" y2="414" stroke="#dcdcdc" stroke-width="1"/>
    <line x1="428" y1="0" x2="428" y2="414" stroke="#dcdcdc" stroke-width="1"/>
  </svg>

  <h2 class="panel-title panel-title--parents">We are parennts of a child with auism</h2>
  <div class="photo photo--round" style="left:48px;top:32px;width:94px;height:94px" role="img" aria-label="Photo of a mother and father smiling together"></div>
  <div class="parents-body lorem">
    <p>Lorem ipsum dolor sit amet, modus legere rationibus has an, veritus definiebas eu eum, mea patrioque cotidieque et. Ex inani adipisci conceptam sit, illique aliquid no nec. Verear interpretaris vituperatoribus ea his, mei ad illum suscipiantur. Solum integre sed ex, cu odio alii vocent cum. Per graece maiorum in, ad posse inani iracundia nec, vim an quaeque scaevola appetere.</p>
    <p>Quo ne aeque nostro prompta, no facilisi voluptatibus vim. Ea duo duis luptatum singulis. Per diceret elaboraret ea, pri graeci eloquentiam te, commune invidunt ne vel. Cum iudico populo molestie ne, ea lorem ubique tincidunt sit.</p>
  </div>
  <div class="photo photo--round" style="left:55px;top:308px;width:90px;height:90px" role="img" aria-label="Photo of a young boy eating green peas"></div>

  <h2 class="stories-title">Maplebrook Success Stories with auism</h2>
  <p class="stories-sub">Helpig You Child Avhieve the Possilbe</p>

  <div class="photo photo--round story-photo" style="left:185px;top:81px" role="img" aria-label="Portrait photo of a smiling child"></div>
  <div class="photo photo--round story-photo" style="left:270px;top:81px" role="img" aria-label="Portrait photo of a smiling child"></div>
  <div class="photo photo--round story-photo" style="left:361px;top:81px" role="img" aria-label="Portrait photo of a smiling child"></div>
  <div class="photo photo--round story-photo" style="left:185px;top:209px" role="img" aria-label="Portrait photo of a smiling child"></div>
  <div class="photo photo--round story-photo" style="left:270px;top:209px" role="img" aria-label="Portrait photo of a smiling child"></div>
  <div class="photo photo--round story-photo" style="left:361px;top:209px" role="img" aria-label="Portrait photo of a smiling child"></div>

  <p class="story" style="left:167px;top:134px">Lorem ipsum dolor sit amet, no nisl imperdiet pri, est assum dignissim cu. Cum et elaboraret cotidieque, fabulas suscipit at per.</p>
  <p class="story" style="left:252px;top:134px">Lorem ipsum dolor sit amet, no nisl imperdiet pri, est assum dignissim cu. Cum et elaboraret cotidieque, fabulas suscipit at per.</p>
  <p class="story" style="left:343px;top:134px">Lorem ipsum dolor sit amet, no nisl imperdiet pri, est assum dignissim cu. Cum et elaboraret cotidieque, fabulas suscipit at per.</p>
  <p class="story" style="left:167px;top:262px">Lorem ipsum dolor sit amet, no nisl imperdiet pri, est assum dignissim cu. Cum et elaboraret cotidieque, fabulas suscipit at per.</p>
  <p class="story" style="left:252px;top:262px">Lorem ipsum dolor sit amet, no nisl imperdiet pri, est assum dignissim cu. Cum et elaboraret cotidieque, fabulas suscipit at per.</p>
  <p class="story" style="left:343px;top:262px">Lorem ipsum dolor sit amet, no nisl imperdiet pri, est assum dignissim cu. Cum et elaboraret cotidieque, fabulas suscipit at per.</p>

  <h3 class="perspective-title">A Parent's Perspetive</h3>
  <p class="perspective-body">Duo eu usique albucius, te suas lisque probatus mel. Cum et elaboraret cotidieque, fabulas suscipit at per. Vim et mellus phaedrum periculaei, et justo mobis deseruisse eum.</p>

  <h2 class="panel-title panel-title--approach">A Child First Approach</h2>
  <p class="approach-lead">Quo ne aeque nostro prompta. No facilisi facilisis voluptatibus vim, vel tale nobis mediocritatem in. Cum iudico populo molestie ne.</p>
  <ul class="approach-list">
    <li>Stet exerci propriae his at, mea novum copiosae ad. Sed ei meliore facilis, alii accusata contentiones mea ad.</li>
    <li>Cetero omittam ius ea, cibo malorum persequeris eos te. Ei sint dicat sit, vis nostrum delicata cu.</li>
    <li>An vim ornatus convenire voluptaria, ut vel minim cetero quaestio.</li>
    <li>Nobis regione accommodare at sed, oportere senserit assueverit ei usu. Alterum expetendis voluptatibus cu quo.</li>
  </ul>
  <div class="photo photo--group" style="left:448px;top:304px;width:126px;height:94px" role="img" aria-label="Photo of a group of smiling children sitting together"></div>
</section>

</body>
</html>
```